Ferncliff Capital - Website Design

We need a website design for a new commercial real estate company called Ferncliff Capital. We're effectively commercial mortgage brokers connecting real estate investors to lenders. We need a website that is simple (not busy), elegant, professional, and user-friendly. A lot of the users will be in their 50's and less tech savvy, so a stream-lined design is best. The website will serve as a portal for lenders to review new financing opportunities, as well as for real estate investors to review terms from lenders.
Updates
Just uploaded our logo.
Target Market(s)
Commercial real estate investors and lenders
Industry/Entity Type
Real Estate
Number of Pages Required
1 page
Colors
Designer to choose colors to be used in the design.
Look and feel

```html
<!DOCTYPE html>
<html lang="en">
<head>
<meta charset="utf-8">
<title>Ferncliff Capital</title>
<link href="https://fonts.googleapis.com/css2?family=Nunito:wght@700&family=Open+Sans:ital,wght@0,400;0,600;1,400;1,600&family=Roboto:wght@400;500&display=swap" rel="stylesheet">
<style>
:root{
  --orange:#e8641b;
  --orange-dark:#c9500f;
  --green:#7aab1c;
  --green-dark:#5f8a10;
  --ink:#2b2b2b;
  --text:#555;
  --muted:#888;
  --footer:#2a2a2a;
  --white:#fff;
}
*{box-sizing:border-box;margin:0;padding:0}
html,body{width:1200px;height:3396px;overflow:hidden}
body{position:relative;background:var(--white);font-family:"Open Sans",Arial,sans-serif;color:var(--text)}
.abs{position:absolute}

/* header */
.site-header{left:0;top:0;width:1200px;height:108px;background:var(--white)}
.brand{left:97px;top:16px;font-family:"Nunito",Arial,sans-serif;font-weight:700;font-size:34px;line-height:38px;color:var(--orange)}
.phone{left:936px;top:12px;font-family:"Roboto",Arial,sans-serif;font-size:22px;color:var(--ink);display:flex;align-items:center;gap:8px}
.main-nav{left:470px;top:56px;display:flex;gap:0;font-family:"Roboto",Arial,sans-serif;font-size:17px;color:#555}
.main-nav a{color:inherit;text-decoration:none;display:block;padding:0 25px;height:52px;line-height:24px}
.main-nav a.active{color:var(--orange);border-bottom:3px solid var(--orange)}

/* hero */
.hero{left:0;top:108px;width:1200px;height:639px;background:linear-gradient(100deg,#4a4f55 0%,#7b8189 35%,#9ea4aa 55%,#6d737a 80%,#3f444a 100%)}
.hero-title{left:0;top:322px;width:1200px;text-align:center;font-family:"Roboto",Arial,sans-serif;color:var(--white);font-size:44px;line-height:52px}
.hero-sub{left:0;top:376px;width:1200px;text-align:center;font-family:"Roboto",Arial,sans-serif;color:var(--white);font-size:36px;line-height:44px}
.btn{display:flex;align-items:center;justify-content:center;font-family:"Roboto",Arial,sans-serif;font-size:16px;color:var(--white);border-radius:3px}
.btn-orange{background:var(--orange)}
.btn-dark{background:var(--ink)}
.hero-btn{left:516px;top:441px;width:170px;height:42px}
.dots{left:553px;top:639px;display:flex;gap:10px}
.dots span{width:14px;height:14px;border-radius:50%;background:var(--white)}
.dots span.off{background:transparent;border:2px solid var(--white)}

/* what we do */
.what-bg{left:0;top:700px;width:1200px;height:440px}
.section-title{font-family:"Roboto",Arial,sans-serif;font-size:32px;letter-spacing:1px;text-align:center;width:1200px;left:0}
.what-title{top:778px;color:var(--ink)}
.what-text{left:200px;top:838px;width:800px;text-align:center;font-size:15px;line-height:25px;color:#777}
.what-btn{left:525px;top:952px;width:147px;height:40px}

/* services */
.services{left:0;top:1007px;width:1200px;height:578px;background:linear-gradient(90deg,#ec6e24 0%,#e8641b 50%,#f07a34 75%,#e45c14 100%)}
.services-photo{left:720px;top:1007px;width:480px;height:578px;background:linear-gradient(160deg,rgba(255,255,255,.18),rgba(255,255,255,0) 60%)}
.services-title{top:1150px;color:var(--white);font-size:30px}
.service{width:290px;height:290px;border-radius:50%;border:5px solid var(--white);box-shadow:0 0 0 3px rgba(255,255,255,.5);display:flex;flex-direction:column;align-items:center;text-align:center;padding-top:50px}
.service.dark{background:var(--ink);color:var(--white)}
.service.light{background:var(--white);color:var(--ink)}
.service h3{font-family:"Roboto",Arial,sans-serif;font-weight:400;font-size:22px;line-height:27px;margin-top:14px}
.service p{font-size:13px;line-height:18px;width:180px;margin-top:8px;color:#888}
.service.dark p{color:#bbb}

/* properties */
.props-title{left:97px;top:1636px;font-family:"Roboto",Arial,sans-serif;font-size:31px;color:var(--orange);letter-spacing:.5px}
.card{top:1702px;width:318px;height:331px;background:var(--ink)}
.card .photo{width:318px;height:222px}
.card h4{position:absolute;left:34px;top:244px;font-family:"Roboto",Arial,sans-serif;font-weight:400;font-size:21px;color:var(--white)}
.card p{position:absolute;left:34px;top:278px;width:230px;font-size:12.5px;line-height:19px;color:#bbb}
.card svg.arrow{position:absolute;right:20px;top:300px}

/* testimonials */
.testimonials{left:0;top:2105px;width:1200px;height:435px;background:linear-gradient(90deg,#7fb11e 0%,#74a519 45%,#6b9a14 70%,#80b120 100%)}
.testi-title{top:2172px;color:var(--white);font-size:30px}
.testi-box{left:242px;top:2255px;width:713px;height:199px;border:1.5px solid rgba(255,255,255,.75);border-radius:16px}
.quote-mark{left:560px;top:2222px;width:80px;height:56px;background:var(--green);display:flex;justify-content:center;align-items:center}
.testi-text{left:265px;top:2290px;width:670px;text-align:center;color:var(--white);font-style:italic;font-size:14px;line-height:25px}
.testi-name{left:0;top:2386px;width:1200px;text-align:center;color:var(--white);font-style:italic;font-weight:600;font-size:15px}
.testi-line{top:2503px;height:3px}

/* why */
.why-photo{left:118px;top:2613px;width:457px;height:292px;background:linear-gradient(135deg,#5a4234 0%,#8c6b55 40%,#d9d4cf 70%,#efece8 100%)}
.why-title{left:623px;top:2614px;font-family:"Roboto",Arial,sans-serif;font-size:30px;color:var(--orange)}
.why-text{left:625px;top:2657px;width:470px;font-size:14px;line-height:24px;color:#666}
.why-list{top:2796px;list-style:none;font-size:13px;line-height:31px;color:#666}
.why-list li{display:flex;align-items:center;gap:12px}

/* footer */
.site-footer{left:0;top:3011px;width:1200px;height:385px;background:var(--footer);color:#ccc}
.f-col{top:3072px}
.f-col h5{font-family:"Roboto",Arial,sans-serif;font-weight:400;font-size:18px;color:var(--white);margin-bottom:16px}
.f-col li{list-style:none;font-size:14px;line-height:29px}
.f-divider{top:3072px;width:1px;height:165px;background:#555}
.f-contact li{display:flex;gap:14px;align-items:flex-start;line-height:22px;margin-bottom:10px}
.social{display:flex;gap:12px}
.social span{width:38px;height:38px;border-radius:50%;background:var(--orange);border:2px solid var(--white)}
.f-rule{left:123px;top:3333px;width:1048px;height:1px;background:#444}
.copyright{left:0;top:3358px;width:1200px;text-align:center;font-size:13px;color:#aaa}
</style>
</head>
<body>

<header class="site-header abs">
  <div class="brand abs">Ferncliff Capital</div>
  <div class="phone abs">
    <svg width="20" height="20" viewBox="0 0 24 24"><path fill="#2a6fb4" d="M6.6 10.8a15.2 15.2 0 0 0 6.6 6.6l2.2-2.2c.3-.3.7-.4 1-.2 1.1.4 2.3.6 3.6.6.6 0 1 .4 1 1V20c0 .6-.4 1-1 1A17 17 0 0 1 3 4c0-.6.4-1 1-1h3.5c.6 0 1 .4 1 1 0 1.3.2 2.5.6 3.6.1.3 0 .7-.2 1z"/></svg>
    (555) 214 7730
  </div>
  <nav class="main-nav abs">
    <a class="active">Home</a><a>About Us</a><a>Our Services</a><a>Property</a><a>Clients</a><a>Contact Us</a>
  </nav>
</header>

<section class="hero abs" role="img" aria-label="Business people looking out of a high-rise office window over city towers"></section>
<svg class="abs" style="left:0;top:640px" width="1200" height="120" viewBox="0 0 1200 120">
  <path d="M0 110 Q600 20 1200 110 L1200 120 L0 120 Z" fill="#e6e6e6"/>
  <path d="M0 114 Q600 34 1200 114 L1200 120 L0 120 Z" fill="#fff"/>
</svg>
<h1 class="hero-title abs" style="font-weight:400">Commercial Mortgage Brokers</h1>
<p class="hero-sub abs">Connecting Real estate Investors to Lenders</p>
<div class="btn btn-orange hero-btn abs">Learn More&nbsp;<svg width="8" height="10" viewBox="0 0 8 10"><path d="M1 0l6 5-6 5z" fill="#fff"/></svg></div>
<div class="dots abs"><span class="off"></span><span></span><span></span><span></span></div>

<section class="services abs"></section>
<div class="services-photo abs" role="img" aria-label="Glass office tower tinted orange"></div>
<svg class="what-bg abs" width="1200" height="440" viewBox="0 0 1200 440">
  <defs><linearGradient id="greyFade" x1="0" y1="0" x2="0" y2="1"><stop offset="0" stop-color="#fff"/><stop offset=".55" stop-color="#f2f2f2"/><stop offset="1" stop-color="#cfcfcf"/></linearGradient></defs>
  <path d="M0 47 H1200 V307 L600 432 L0 307 Z" fill="url(#greyFade)"/>
</svg>
<h2 class="section-title what-title abs" style="font-weight:400">WHAT WE DO</h2>
<p class="what-text abs">When subdividing /developing properties there is a long list of conditions, costs, time restraints, varying stages; foresee pitfalls and problems. Design, Applications, Demolition, Site works, Services, Surveyors, Agents ...the list goes What to do and when... We'll handle it for you..</p>
<div class="btn btn-dark what-btn abs">Learn More</div>

<h2 class="section-title services-title abs" style="font-weight:400">OUR SERVICES</h2>
<div class="service dark abs" style="left:138px;top:1220px">
  <svg width="76" height="76" viewBox="0 0 76 76" fill="none" stroke="#fff" stroke-width="2.5">
    <path d="M38 6l6 8 10-2 2 10 9 5-4 9 4 9-9 5-2 10-10-2-6 8-6-8-10 2-2-10-9-5 4-9-4-9 9-5 2-10 10 2z"/>
    <circle cx="38" cy="32" r="7"/><path d="M26 50c2-7 7-10 12-10s10 3 12 10"/>
  </svg>
  <h3>Mortgage Services</h3>
  <p>Morbi diam mauris viverra in gravida eu mattis in ante Morbi eget arcu Morbi</p>
</div>
<div class="service light abs" style="left:462px;top:1220px">
  <svg width="90" height="70" viewBox="0 0 90 70" fill="none" stroke="#e8641b" stroke-width="2.5">
    <circle cx="22" cy="40" r="7"/><path d="M8 64c1-9 7-13 14-13s13 4 14 13"/>
    <circle cx="68" cy="40" r="7"/><path d="M54 64c1-9 7-13 14-13s13 4 14 13"/>
    <path d="M24 22a24 24 0 0 1 42 0"/><circle cx="38" cy="40" r="1.5" fill="#e8641b"/><circle cx="45" cy="40" r="1.5" fill="#e8641b"/><circle cx="52" cy="40" r="1.5" fill="#e8641b"/>
  </svg>
  <h3>Connecting<br>Investor to Lenders</h3>
  <p>Morbi diam mauris viverra in gravida eu mattis in ant</p>
</div>
<div class="service light abs" style="left:783px;top:1220px">
  <svg width="60" height="76" viewBox="0 0 60 76"><rect x="12" y="10" width="36" height="64" fill="#e8641b"/><rect x="24" y="2" width="12" height="10" fill="#e8641b"/>
    <g fill="#fff"><rect x="17" y="18" width="6" height="6"/><rect x="27" y="18" width="6" height="6"/><rect x="37" y="18" width="6" height="6"/><rect x="17" y="30" width="6" height="6"/><rect x="27" y="30" width="6" height="6"/><rect x="37" y="30" width="6" height="6"/><rect x="17" y="42" width="6" height="6"/><rect x="27" y="42" width="6" height="6"/><rect x="37" y="42" width="6" height="6"/><rect x="25" y="58" width="10" height="16"/></g></svg>
  <h3>Commercial<br>Real Estate</h3>
  <p>Morbi diam mauris viverra in gravida eu mattis in ant</p>
</div>

<h2 class="props-title abs" style="font-weight:400">LATEST PROPERTIES</h2>
<article class="card abs" style="left:102px">
  <div class="photo" role="img" aria-label="Modern glass office building under blue sky" style="background:linear-gradient(180deg,#8fb6de 0%,#c9d9e6 50%,#6f7c86 100%)"></div>
  <h4>Property Title here</h4><p>Morbi diam mauris viverra in gravida eu mattis in ante Morbi eget arcu</p>
  <svg class="arrow" width="18" height="14" viewBox="0 0 18 14"><path d="M1 7h15M10 1l6 6-6 6" stroke="#fff" stroke-width="1.6" fill="none"/></svg>
</article>
<article class="card abs" style="left:446px">
  <div class="photo" role="img" aria-label="White office block with a green tree in front" style="background:linear-gradient(180deg,#3f86d8 0%,#9cc3ea 40%,#d7dde2 70%,#6e9a4c 100%)"></div>
  <h4>Property Title here</h4><p>Morbi diam mauris viverra in gravida eu mattis in ante Morbi eget arcu</p>
  <svg class="arrow" width="18" height="14" viewBox="0 0 18 14"><path d="M1 7h15M10 1l6 6-6 6" stroke="#fff" stroke-width="1.6" fill="none"/></svg>
</article>
<article class="card abs" style="left:788px">
  <div class="photo" role="img" aria-label="Stone and brick retail building with parking lot" style="background:linear-gradient(180deg,#e9ecef 0%,#b59b84 45%,#7b5a45 70%,#9a9a9a 100%)"></div>
  <h4>Property Title here</h4><p>Morbi diam mauris viverra in gravida eu mattis in ante Morbi eget arcu</p>
  <svg class="arrow" width="18" height="14" viewBox="0 0 18 14"><path d="M1 7h15M10 1l6 6-6 6" stroke="#fff" stroke-width="1.6" fill="none"/></svg>
</article>

<section class="testimonials abs" role="img" aria-label="Business meeting scene tinted green"></section>
<h2 class="section-title testi-title abs" style="font-weight:400">TESTIMONIALS</h2>
<div class="testi-box abs"></div>
<div class="quote-mark abs"><svg width="52" height="40" viewBox="0 0 52 40" fill="#fff"><path d="M4 0h18v18c0 12-6 20-17 22l-2-5c6-2 9-6 9-11H4z"/><path d="M30 0h18v18c0 12-6 20-17 22l-2-5c6-2 9-6 9-11h-8z"/></svg></div>
<p class="testi-text abs">"Sed ut perspiciatis unde omnis iste natus error sit voluptatem accusantium doloremque laudantium, totam rem aperiam, eaque ipsa quae ab illo inventore veritatis et quasi architecto beatae vitae dicta sunt explicabo. Nemo enim ipsam voluptatem quia voluptas sit aspernatur aut odit aut consequuntur .</p>
<p class="testi-name abs">Mark Ellison - Riverton Credit Union</p>
<svg class="abs" style="left:160px;top:2320px" width="26" height="42" viewBox="0 0 26 42"><path d="M22 3L5 21l17 18" stroke="#fff" stroke-width="4" fill="none"/></svg>
<svg class="abs" style="left:1000px;top:2320px" width="26" height="42" viewBox="0 0 26 42"><path d="M4 3l17 18L4 39" stroke="#fff" stroke-width="4" fill="none"/></svg>
<div class="testi-line abs" style="left:557px;width:30px;background:#fff"></div>
<div class="testi-line abs" style="left:590px;width:52px;background:rgba(255,255,255,.45)"></div>

<div class="why-photo abs" role="img" aria-label="Handshake over a desk with contract papers and a pen"></div>
<h2 class="why-title abs" style="font-weight:400">WHY CHOOSE US</h2>
<p class="why-text abs">interdum vel blandit sed nulla In ullamcorper est eget tempor cursus neque mi consectetuer mi a ultricies massa est sed nisl Class aptent taciti sociosqu ad litora torquent per conubia nostra per inceptos hymenaeos Proin nulla arcu nonummy luctus</p>
<ul class="why-list abs" style="left:629px">
  <li><svg width="7" height="11" viewBox="0 0 7 11"><path d="M1 1l4.5 4.5L1 10" stroke="#e8641b" stroke-width="2" fill="none"/></svg>Aymenaeos Proin nulla arcu</li>
  <li><svg width="7" height="11" viewBox="0 0 7 11"><path d="M1 1l4.5 4.5L1 10" stroke="#e8641b" stroke-width="2" fill="none"/></svg>nonummy luctus dictum eget ferme</li>
  <li><svg width="7" height="11" viewBox="0 0 7 11"><path d="M1 1l4.5 4.5L1 10" stroke="#e8641b" stroke-width="2" fill="none"/></svg>et lorem Nunc porta</li>
</ul>
<ul class="why-list abs" style="left:901px">
  <li><svg width="7" height="11" viewBox="0 0 7 11"><path d="M1 1l4.5 4.5L1 10" stroke="#e8641b" stroke-width="2" fill="none"/></svg>Praesent elementum elit</li>
  <li><svg width="7" height="11" viewBox="0 0 7 11"><path d="M1 1l4.5 4.5L1 10" stroke="#e8641b" stroke-width="2" fill="none"/></svg>At tellus Curabitur</li>
  <li><svg width="7" height="11" viewBox="0 0 7 11"><path d="M1 1l4.5 4.5L1 10" stroke="#e8641b" stroke-width="2" fill="none"/></svg>Metus ipsum luctus</li>
</ul>

<footer class="site-footer abs"></footer>
<div class="f-col abs" style="left:113px"><h5>COMPANY</h5><ul><li>Home</li><li>About Us</li><li>Our Clients</li><li>Why Us</li></ul></div>
<div class="f-divider abs" style="left:267px"></div>
<div class="f-col abs" style="left:317px"><h5>RESOURCES</h5><ul><li>Our Services</li><li>Testimonials</li><li>Blogs</li><li>Contact Us</li></ul></div>
<div class="f-divider abs" style="left:464px"></div>
<div class="f-col f-contact abs" style="left:518px"><h5>CONTACT US</h5><ul>
  <li><svg width="14" height="20" viewBox="0 0 14 20"><path d="M7 0a7 7 0 0 0-7 7c0 5 7 13 7 13s7-8 7-13a7 7 0 0 0-7-7zm0 10a3 3 0 1 1 0-6 3 3 0 0 1 0 6z" fill="#fff"/></svg><span>42 Orchard Lane, Westmere,<br>Northdale, NL4 2RT</span></li>
  <li><svg width="16" height="16" viewBox="0 0 24 24"><path fill="#fff" d="M6.6 10.8a15.2 15.2 0 0 0 6.6 6.6l2.2-2.2c.3-.3.7-.4 1-.2 1.1.4 2.3.6 3.6.6.6 0 1 .4 1 1V20c0 .6-.4 1-1 1A17 17 0 0 1 3 4c0-.6.4-1 1-1h3.5c.6 0 1 .4 1 1 0 1.3.2 2.5.6 3.6.1.3 0 .7-.2 1z"/></svg><span>07700 900418</span></li>
  <li><svg width="16" height="12" viewBox="0 0 16 12"><rect width="16" height="12" rx="1" fill="#fff"/><path d="M0 1l8 6 8-6" stroke="#2a2a2a" stroke-width="1.5" fill="none"/></svg><span>hello@ferncliffcapital.example</span></li>
</ul></div>
<div class="f-divider abs" style="left:788px"></div>
<div class="f-col abs" style="left:831px"><h5>FOLLOW US</h5>
  <div class="social" aria-label="Social media links"><span></span><span></span><span></span><span></span></div>
</div>
<div class="f-rule abs"></div>
<p class="copyright abs">© 2017 Ferncliff Capital. All right reserved</p>

</body>
</html>
```